Images and design ideas provided: Postcard size flier

2 sided postcard size flier to hand people on the street.

A FUN tax business needs a postcard size flier to hand people on the street. Not a typical serious, quiet, office so make the image fun!

Exact wording, logo and key images provided. You are free to add other images as you see fit (such as money).

Side 1: Use image of lady looking up (she should be looking at text provided).All spanish and english text provided. Logo in bottom right corner. Address at bottom of card.

Side 2: Image of lady holding money and pointing. Remove money and have her holding a sign/or some other creative way to have her looking at text. All spanish and english text provided. Logo in bottom right corner. Address at bottom of card.

Size: 4" x 6" horizontal or vertical is ok
Each side can be different and image/design does not have to be related.

Target Market(s)

Age 18-35

Industry/Entity Type

Accounting

Font styles to use
Sans Serif

Colors

Designer to choose colors to be used in the design.

Requirements
Must have
• Use text document provided. All text goes on both sides.
• Should be easy to read from a few feet away.
Nice to have
• Bright colors to attract attention of people walking by to grab flier/card. Images of money ok.
Should not have
• No images of calculators or typical accounting tax forms.

```html
<!DOCTYPE html>
<html lang="en">
<head>
<meta charset="utf-8">
<title>Northgate Tax Studio – Postcard Flier</title>
<link rel="stylesheet" href="https://fonts.googleapis.com/css2?family=Fjalla+One&family=Michroma&family=Open+Sans:wght@400;600&family=Roboto+Condensed:wght@400&display=swap">
<style>
  :root {
    --page-bg: #2b2b2b;
    --sky-deep: #5ec3e6;
    --sky-light: #e6f6fb;
    --paper: #ffffff;
    --stripe: #4a4a4a;
    --brand-blue: #3b6cb5;
    --brand-red: #e2213f;
    --ink: #2e2e2e;
    --photo-a: #b8a06a;
    --photo-b: #7d8a55;
    --photo-c: #b5313a;
  }
  * { margin: 0; padding: 0; box-sizing: border-box; }
  html, body { width: 845px; height: 1200px; overflow: hidden; background: var(--page-bg); }
  .canvas {
    width: 845px; height: 1200px;
    display: flex; flex-direction: column; justify-content: space-evenly; align-items: center;
  }
  .postcard { width: 760px; height: 507px; display: block; box-shadow: 0 6px 18px rgba(0,0,0,.45); }
  .headline { font-family: "Fjalla One", sans-serif; font-size: 64px; fill: var(--brand-blue); stroke: var(--paper); stroke-width: 3px; paint-order: stroke; }
  .subline { font-family: "Open Sans", sans-serif; font-size: 27px; fill: var(--ink); }
  .spanish-headline { font-family: "Michroma", sans-serif; font-size: 30px; fill: var(--brand-red); stroke: var(--brand-red); stroke-width: 1px; }
  .spanish-subline { font-family: "Roboto Condensed", sans-serif; font-size: 19px; fill: var(--ink); }
  .brand-name { font-family: "Fjalla One", sans-serif; font-size: 30px; fill: var(--ink); }
  .phone { font-family: "Fjalla One", sans-serif; font-size: 34px; fill: var(--paper); }
  .address { font-family: "Fjalla One", sans-serif; font-size: 22px; fill: var(--paper); }
</style>
</head>
<body>
<main class="canvas">

  <!-- Side 1 -->
  <svg class="postcard" viewBox="0 0 760 507" xmlns="http://www.w3.org/2000/svg" aria-label="Postcard side one">
    <defs>
      <linearGradient id="sky1" x1="0" y1="0" x2="1" y2="1">
        <stop offset="0" stop-color="var(--sky-deep)"/>
        <stop offset=".6" stop-color="var(--sky-light)"/>
      </linearGradient>
      <linearGradient id="photo1" x1="0" y1="0" x2="0" y2="1">
        <stop offset="0" stop-color="var(--photo-a)"/>
        <stop offset=".55" stop-color="var(--photo-b)"/>
        <stop offset="1" stop-color="var(--photo-c)"/>
      </linearGradient>
    </defs>
    <rect class="sky" width="760" height="507" fill="url(#sky1)"/>
    <polygon class="paper" points="0,250 520,236 620,205 760,160 760,507 0,507" fill="var(--paper)"/>
    <polygon class="stripe" points="0,212 480,228 480,244 0,228" fill="var(--stripe)"/>
    <polygon class="stripe" points="580,185 760,140 760,158 580,203" fill="var(--stripe)"/>
    <rect class="photo" x="0" y="80" width="330" height="370" rx="6" fill="url(#photo1)" role="img" aria-label="Photo of a cheerful woman in a costume looking up at the headline with arms raised"/>
    <polygon class="stripe" points="0,398 128,356 640,507 600,507 128,372 0,414" fill="var(--stripe)"/>
    <polygon class="contact-band" points="0,412 128,372 600,507 0,507" fill="var(--brand-red)"/>

    <text class="headline" x="52" y="80" textLength="620" lengthAdjust="spacingAndGlyphs">GET $100 CASH NOW!</text>
    <text class="subline" x="222" y="130" textLength="346">with paid tax preparation</text>
    <text class="spanish-headline" x="332" y="274" textLength="394" lengthAdjust="spacingAndGlyphs">RECIBA $100 EN</text>
    <text class="spanish-headline" x="332" y="314" textLength="394" lengthAdjust="spacingAndGlyphs">EFECTIVO AHORA!</text>
    <text class="spanish-subline" x="332" y="347" textLength="394" lengthAdjust="spacingAndGlyphs">CON LA PREPARACION PAGADA DE SUS IMPUESTOS</text>

    <text class="brand-name" x="726" y="422" text-anchor="end">Northgate Tax Studio</text>

    <g class="icon-phone" fill="none" stroke="var(--paper)" stroke-width="2">
      <circle cx="35" cy="440" r="10"/>
      <path d="M31 435 q0 9 9 10 l1-3 -3-1 -1 1 q-3-1 -4-4 l1-1 -1-3z" fill="var(--paper)" stroke="none"/>
    </g>
    <text class="phone" x="57" y="453">(555) 014-2276</text>
    <g class="icon-pin" fill="none" stroke="var(--paper)" stroke-width="2">
      <circle cx="35" cy="478" r="10"/>
      <path d="M35 484 q-5-6 -5-9 a5 5 0 0 1 10 0 q0 3 -5 9z" fill="var(--paper)" stroke="none"/>
    </g>
    <text class="address" x="57" y="486">418 Maple Ave. Riverton NY 10000</text>
  </svg>

  <!-- Side 2 -->
  <svg class="postcard" viewBox="0 0 760 507" xmlns="http://www.w3.org/2000/svg" aria-label="Postcard side two">
    <defs>
      <linearGradient id="sky2" x1="0" y1="0" x2="1" y2="1">
        <stop offset="0" stop-color="var(--sky-deep)"/>
        <stop offset=".6" stop-color="var(--sky-light)"/>
      </linearGradient>
      <linearGradient id="photo2" x1="0" y1="0" x2="0" y2="1">
        <stop offset="0" stop-color="var(--photo-c)"/>
        <stop offset=".3" stop-color="var(--photo-a)"/>
        <stop offset=".75" stop-color="var(--photo-b)"/>
        <stop offset="1" stop-color="var(--photo-c)"/>
      </linearGradient>
    </defs>
    <rect class="sky" width="760" height="507" fill="url(#sky2)"/>
    <polygon class="paper" points="0,250 520,236 620,205 760,160 760,507 0,507" fill="var(--paper)"/>
    <polygon class="stripe" points="0,212 480,228 480,244 0,228" fill="var(--stripe)"/>
    <polygon class="stripe" points="580,185 760,140 760,158 580,203" fill="var(--stripe)"/>
    <rect class="photo" x="0" y="20" width="330" height="410" rx="6" fill="url(#photo2)" role="img" aria-label="Photo of an excited woman in a costume holding cash and pointing toward the headline"/>
    <polygon class="stripe" points="0,398 128,356 640,507 600,507 128,372 0,414" fill="var(--stripe)"/>
    <polygon class="contact-band" points="0,412 128,372 600,507 0,507" fill="var(--brand-red)"/>

    <text class="headline" x="142" y="72" textLength="550" lengthAdjust="spacingAndGlyphs">GET $100 CASH NOW!</text>
    <text class="subline" x="342" y="114" textLength="304">with paid tax preparation</text>
    <text class="spanish-headline" x="338" y="284" textLength="394" lengthAdjust="spacingAndGlyphs">RECIBA $100 EN</text>
    <text class="spanish-headline" x="338" y="324" textLength="394" lengthAdjust="spacingAndGlyphs">EFECTIVO AHORA!</text>
    <text class="spanish-subline" x="338" y="358" textLength="394" lengthAdjust="spacingAndGlyphs">CON LA PREPARACION PAGADA DE SUS IMPUESTOS</text>

    <text class="brand-name" x="736" y="434" text-anchor="end">Northgate Tax Studio</text>

    <g class="icon-phone" fill="none" stroke="var(--paper)" stroke-width="2">
      <circle cx="35" cy="440" r="10"/>
      <path d="M31 435 q0 9 9 10 l1-3 -3-1 -1 1 q-3-1 -4-4 l1-1 -1-3z" fill="var(--paper)" stroke="none"/>
    </g>
    <text class="phone" x="57" y="453">(555) 014-2276</text>
    <g class="icon-pin" fill="none" stroke="var(--paper)" stroke-width="2">
      <circle cx="35" cy="478" r="10"/>
      <path d="M35 484 q-5-6 -5-9 a5 5 0 0 1 10 0 q0 3 -5 9z" fill="var(--paper)" stroke="none"/>
    </g>
    <text class="address" x="57" y="486">418 Maple Ave. Riverton NY 10000</text>
  </svg>

</main>
</body>
</html>
```